We need UI/UX design for a public, informational website for The Copper Lantern.
The pages, structure, and content scope are already defined. Designers are required to work only on the UI/UX layout of these existing pages, focusing on clarity, hierarchy, spacing, and usability. Do not add, remove, rename, or reinterpret pages or content.
The website is strictly informational only. It must not include accounts, onboarding, payments, custody, escrow administration, marketplaces, dashboards, or any transactional functionality.
Scope of work
Apply UI/UX design to the predefined website pages
Design layout for text, images, notices, and sections
Ensure consistent components and layout patterns across page types
Optimize layouts for long form, compliance focused content
Content writing, page creation, and branding changes are out of scope.
Structure reference
The complete page list, hierarchy, and content definitions are provided in the technical documentation and must be treated as the primary source of truth.
A Figma link is provided only as a light visual reference for page existence and structure:
https://meadow-knot-48203956.plumsite.example/
Designers must rely on the documentation for in depth and authoritative reference.
Brand guidelines
The Copper Lantern has existing brand guidelines and official logos, including light and dark versions. These assets will be provided and must be followed exactly. Designers must not redesign, alter, or reinterpret the brand identity.
Look and feel direction
The desired visual direction is inspired by:
https://ledgerwaltz.example/
This reference is provided only to indicate:
Institutional and enterprise tone
Clean, modern typography
Strong hierarchy and generous whitespace
Editorial, content first layouts
Do not copy branding, layouts, components, or assets from the reference site.
Hero section direction
The hero section should follow a similar structural approach to the hero used on https://ledgerwaltz.example/
, meaning:
Strong editorial framing
Clear headline hierarchy
Calm, institutional first impression
However, the background video must be Abu Dhabi focused, not generic or global. The video should visually reflect:
Abu Dhabi skyline or architectural language
Institutional, sovereign, long term infrastructure tone
Clean, slow, cinematic motion
No promotional, marketing, or lifestyle visuals
The hero must remain informational, restrained, and credible. No hype. No calls to invest. No implied participation.
Constraints
One global primary CTA only: “Continue to Halvemark” (external)
All other interactions must be informational
No visuals or language implying offers, investment, eligibility, or participation
Clear separation between informational content and any external operational platforms
Deliverables
High fidelity UI/UX designs created in Figma, covering:
Desktop layouts
Tablet layouts where relevant
Mobile layouts
Complete Figma file(s) including:
All designed pages defined in the technical documentation
A reusable component library (headers, footers, cards, notice panels, forms, CTAs, typography styles, spacing system)
Clearly defined layout grids, spacing rules, and text styles
Proper use of components and variants, not detached frames
Designs prepared for developer handoff, including:
Clear layer naming and structure
Auto layout where appropriate
Consistent use of styles and components
Responsive behavior demonstrated within Figma
Notes or annotations only where necessary for clarity
No prototypes, interactions, or motion design beyond basic layout states, unless explicitly requested. The focus is static UI/UX clarity, not animation.
A detailed technical specification document and official brand assets will be provided.
Any designs delivered outside Figma, that alter structure or content, or that ignore the defined constraints, boundaries, or tone will be rejected.

```html
<!DOCTYPE html>
<html lang="en">
<head>
<meta charset="utf-8">
<title>The Copper Lantern — Governance Framework</title>
<link href="https://fonts.googleapis.com/css2?family=Onest:wght@300;400;500;600&display=swap" rel="stylesheet">
<style>
:root{
  --backdrop:#b6b6b6;
  --ink:#111111;
  --white:#ffffff;
  --paper:#f6f6f6;
  --charcoal:#383838;
  --graphite:#303030;
  --night:#1c1c1c;
  --black:#000000;
  --muted-dark:#b9b9b9;
  --muted-light:#6a6a6a;
  --rule-dark:#4a4a4a;
  --rule-light:#dddddd;
}
*{box-sizing:border-box;margin:0;padding:0}
html,body{width:1200px;height:3250px;overflow:hidden}
body{background:var(--backdrop);font-family:"Onest",Arial,sans-serif;color:var(--ink)}
.page{position:absolute;left:81px;top:81px;width:1037px}
section,footer{position:relative;width:100%}
.inner{position:absolute;left:148px;width:742px}
.pill{display:inline-block;background:var(--white);color:var(--ink);border-radius:20px;font-weight:500;white-space:nowrap}
.photo{background:linear-gradient(160deg,#8c8c8c,#3d3d3d)}

/* hero */
.hero{height:589px;background:linear-gradient(180deg,#3a3a3a 0%,#2b2b2b 45%,#262626 100%);color:var(--white);overflow:hidden}
.hero-photo{position:absolute;inset:0;background:radial-gradient(ellipse at 25% 35%,rgba(120,120,120,.55),transparent 55%),linear-gradient(180deg,#4a4a4a 0%,#2e2e2e 60%,#262626 100%)}
.brand{position:absolute;left:15px;top:28px;font-size:12px;font-weight:500;letter-spacing:.02em;white-space:nowrap}
.nav{position:absolute;left:0;right:0;top:20px;display:flex;justify-content:center;gap:24px;font-size:10px;color:#d6d6d6}
.nav .current{color:var(--white);font-weight:500}
.nav-cta{position:absolute;right:11px;top:11px;font-size:9.5px;padding:5px 10px}
.hero-copy{position:absolute;left:0;right:0;top:302px;text-align:center}
.hero-copy h1{font-size:36px;font-weight:500;line-height:45px;letter-spacing:-.01em}
.hero-copy p{margin-top:12px;font-size:17.5px;font-weight:300;line-height:26px;color:#e8e8e8}
.hero-copy .pill{margin-top:16px;font-size:11.5px;padding:6px 14px}

/* about */
.about{height:377px;background:var(--charcoal);color:var(--white)}
.about .inner{top:82px}
.eyebrow{font-size:10px;color:var(--muted-dark)}
.about h2{margin-top:5px;font-size:28px;font-weight:500;line-height:32px;width:360px}
.about p{margin-top:10px;font-size:8.8px;line-height:15px;color:var(--muted-dark);width:352px}
.about .pill{margin-top:12px;font-size:11px;padding:6px 14px}
.about-tiles{position:absolute;left:544px;top:82px;width:346px;height:213px;display:flex;gap:5px}
.tile{flex:1;position:relative;color:var(--white);font-size:11px;line-height:13px}
.tile span{position:absolute;left:12px;bottom:12px}

/* role */
.role{height:537px;background:var(--paper)}
.center-head{position:absolute;left:0;right:0;text-align:center}
.role .eyebrow{color:var(--muted-light)}
.section-title{font-size:28px;font-weight:500;letter-spacing:-.01em}
.cards-3{position:absolute;left:148px;top:145px;width:742px;display:flex;gap:25px}
.role-card{flex:1;height:310px;background:var(--white)}
.role-card .photo{height:141px}
.role-card .body{padding:15px 19px}
.role-card h3{font-size:18px;font-weight:500}
.role-card p{margin-top:5px;font-size:8.6px;line-height:12.5px;color:var(--muted-light);height:40px}
.meta{margin-top:8px;font-size:8.6px}
.meta div{display:flex;padding:6px 0 5px;border-bottom:1px solid var(--rule-light)}
.meta dt{width:60px;color:var(--muted-light)}
.meta dd{font-weight:600}

/* framework */
.framework{height:375px;background:var(--black);color:var(--white)}
.framework .intro{position:absolute;left:148px;top:87px;width:230px}
.framework h2{margin-top:8px;font-size:29px;font-weight:500}
.framework .intro p{margin-top:10px;font-size:9.5px;line-height:15px;color:#d8d8d8}
.principles{position:absolute;left:467px;top:87px;width:423px}
.principles .num{font-size:9px;color:var(--muted-dark)}
.principles h3{margin-top:6px;font-size:18px;font-weight:500}
.principles .lead{margin-top:4px;font-size:8.6px;line-height:11.5px;color:var(--muted-dark);padding-bottom:14px;border-bottom:1px solid var(--rule-dark)}
.accordion li{list-style:none;display:flex;justify-content:space-between;align-items:center;height:32.5px;font-size:17px;border-bottom:1px solid var(--rule-dark)}
.accordion li span{font-size:15px}

/* reviewers */
.reviewers{height:332px;background:var(--paper)}
.cards-4{position:absolute;left:148px;top:117px;width:742px;display:flex;gap:20px}
.rev-card{flex:1;height:143px;border:2px solid #e6e6e6;background:var(--paper);position:relative;padding:20px 18px}
.rev-card h3{font-size:13.5px;font-weight:500;line-height:17px}
.rev-card p{margin-top:7px;font-size:8.5px;line-height:13px;color:var(--muted-light)}
.rev-card::after{content:"";position:absolute;right:0;bottom:0;width:17px;height:14px;background:#e2e2e2}

/* why */
.why{height:374px;background:var(--charcoal);color:var(--white)}
.why-grid{position:absolute;left:148px;top:113px;width:742px;display:grid;grid-template-columns:1fr 1fr}
.why-item{height:96px;text-align:center;padding:23px 24px 0}
.why-item:nth-child(odd){border-right:1px solid var(--rule-dark)}
.why-item:nth-child(-n+2){border-bottom:1px solid var(--rule-dark)}
.why-item h3{font-size:13.5px;font-weight:500}
.why-item p{margin-top:6px;font-size:8.6px;line-height:12.5px;color:var(--muted-dark)}

/* cta */
.cta{height:292px;background:var(--night);color:var(--white);text-align:center}
.cta .center-head{top:58px}
.cta .eyebrow{font-size:10px;color:#cfcfcf;letter-spacing:.02em}
.cta h2{margin-top:8px;font-size:27px;font-weight:400;line-height:30px;text-transform:uppercase}
.cta p{margin-top:8px;font-size:10.5px;line-height:16px;color:#cfcfcf}
.cta .dark-btn{display:inline-block;margin-top:10px;background:var(--black);color:var(--white);border-radius:20px;font-size:11px;font-weight:500;padding:6px 16px}

/* footer */
.site-footer{height:211px;background:var(--black);color:var(--white)}
.foot-cols{position:absolute;left:190px;top:14px;width:680px;display:flex}
.foot-col{width:168px}
.foot-col h4{font-size:9.5px;font-weight:500;margin-bottom:10px}
.foot-col p,.foot-col li{font-size:7.5px;line-height:15px;color:#cfcfcf;list-style:none}
.foot-col p{line-height:11px;width:145px}
.foot-rule{position:absolute;left:190px;top:135px;width:658px;border-top:1px solid #2a2a2a}
.foot-legal{position:absolute;left:190px;top:146px;width:658px;font-size:7.5px;line-height:11px;color:#a6a6a6}
.foot-legal p+p{margin-top:6px}
</style>
</head>
<body>
<main class="page">

  <section class="hero">
    <div class="hero-photo" role="img" aria-label="Aerial photograph of the Abu Dhabi skyline with dense towers, darkened"></div>
    <div class="brand">THE COPPER LANTERN</div>
    <nav class="nav">
      <span class="current">Home</span><span>Framework</span><span>Projects</span><span>Company</span><span>Insights</span><span>Contact</span>
    </nav>
    <span class="pill nav-cta">Continue to Halvemark</span>
    <div class="hero-copy">
      <h1>A Governance Framework for<br>Structured Project Oversight</h1>
      <p>Clear boundaries. Institutional discipline. Transparent<br>structures for managing risk and accountability.</p>
      <span class="pill">Learn the Framework</span>
    </div>
  </section>

  <section class="about">
    <div class="inner">
      <div class="eyebrow">About The Copper Lantern</div>
      <h2>From Governance Frameworks to Intelligent Infrastructure</h2>
      <p>The Copper Lantern is a governance and project origination group focused on defining structural standards for complex initiatives. We publish clear frameworks that explain role separation, accountability, and long-term oversight across governance, operations, and project-level execution.</p>
      <span class="pill">Our Framework</span>
    </div>
    <div class="about-tiles">
      <div class="tile photo" role="img" aria-label="Black and white city street view between buildings"><span>Independent Oversight<br>Principles</span></div>
      <div class="tile photo" role="img" aria-label="Black and white modern tower with circular architecture"><span>Institutional-Grade<br>Standards</span></div>
    </div>
  </section>

  <section class="role">
    <div class="center-head" style="top:82px">
      <div class="eyebrow">Role Clarity</div>
      <h2 class="section-title" style="margin-top:2px">Understanding Our Role</h2>
    </div>
    <div class="cards-3">
      <article class="role-card">
        <div class="photo" role="img" aria-label="Black and white classical columned government building"></div>
        <div class="body">
          <h3>Governance</h3>
          <p>We define structural frameworks, role boundaries, and oversight mechanisms. This is our domain.</p>
          <dl class="meta">
            <div><dt>Category</dt><dd>Governance Framework</dd></div>
            <div><dt>Audience</dt><dd>Institutional &amp; Public Reference</dd></div>
            <div><dt>Disclosure</dt><dd>Informational Use Only *</dd></div>
          </dl>
        </div>
      </article>
      <article class="role-card">
        <div class="photo" role="img" aria-label="Black and white modern high-rise facades with palm trees"></div>
        <div class="body">
          <h3>Operations</h3>
          <p>Day-to-day execution and project management occur outside our organization, through Halvemark.</p>
          <dl class="meta">
            <div><dt>Category</dt><dd>Governance Framework</dd></div>
            <div><dt>Audience</dt><dd>Institutional &amp; Public Reference</dd></div>
            <div><dt>Disclosure</dt><dd>Informational Use Only *</dd></div>
          </dl>
        </div>
      </article>
      <article class="role-card">
        <div class="photo" role="img" aria-label="Black and white waterfront skyline of towers"></div>
        <div class="body">
          <h3>Transactions</h3>
          <p>We do not facilitate, execute, or participate in any financial transactions or operational activities.</p>
          <dl class="meta">
            <div><dt>Category</dt><dd>Governance Framework</dd></div>
            <div><dt>Audience</dt><dd>Institutional &amp; Public Reference</dd></div>
            <div><dt>Disclosure</dt><dd>Informational Use Only *</dd></div>
          </dl>
        </div>
      </article>
    </div>
  </section>

  <section class="framework">
    <div class="intro">
      <div class="eyebrow">Core Governance Principles</div>
      <h2>The Framework</h2>
      <p>A structured set of principles defining oversight, accountability, and role separation.</p>
    </div>
    <div class="principles">
      <div class="num">01</div>
      <h3>Role Boundaries</h3>
      <p class="lead">Clear separation between governance responsibilities, operational platforms, and project-level execution to prevent overlap and ambiguity.</p>
      <ul class="accordion">
        <li>SPV Structure<span>+</span></li>
        <li>Escrow Model<span>+</span></li>
        <li>Records and Registers<span>+</span></li>
        <li>Risk and Boundaries<span>+</span></li>
      </ul>
    </div>
  </section>

  <section class="reviewers">
    <div class="center-head" style="top:62px"><h2 class="section-title">For Framework Reviewers</h2></div>
    <div class="cards-4">
      <article class="rev-card"><h3>Review Governance Structures</h3><p>Explore published frameworks outlining governance models, role separation, and accountability principles.</p></article>
      <article class="rev-card"><h3>Defined Structural Ownership</h3><p>Frameworks clarify responsibility and authority boundaries without operational or transactional execution.</p></article>
      <article class="rev-card"><h3>Operational Independence</h3><p>Execution, asset handling, and platform operations occur outside this site through independent entities.</p></article>
      <article class="rev-card"><h3>Clear Access Boundaries</h3><p>This site provides documentation and reference materials only—no onboarding, custody, or execution.</p></article>
    </div>
  </section>

  <section class="why">
    <div class="center-head" style="top:66px"><h2 class="section-title">Why The Copper Lantern</h2></div>
    <div class="why-grid">
      <div class="why-item"><h3>Governance-First Approach</h3><p>We prioritize structural clarity and accountability, treating governance as the foundation—not an afterthought.</p></div>
      <div class="why-item"><h3>Proven Structural Principles</h3><p>Our frameworks are informed by institutional standards across governance, compliance, and long-term infrastructure design.</p></div>
      <div class="why-item"><h3>Bridging Structure &amp; Execution</h3><p>We define governance and role boundaries while execution occurs independently through separate operational platforms.</p></div>
      <div class="why-item"><h3>Defined Control &amp; Boundaries</h3><p>Clear limitations ensure responsibilities remain properly scoped, auditable, and enforceable.</p></div>
    </div>
  </section>

  <section class="cta">
    <div class="center-head">
      <div class="eyebrow">FOR PROJECT ORIGINATORS</div>
      <h2>Define your project’s<br>governance framework</h2>
      <p>Design clear structural roles, accountability boundaries, and oversight<br>principles before operational execution begins.</p>
      <span class="dark-btn">Start a Framework Discussion</span>
    </div>
  </section>

  <footer class="site-footer">
    <div class="foot-cols">
      <div class="foot-col"><h4>The Copper Lantern</h4><p>A governance framework for structured project oversight and risk management.</p></div>
      <div class="foot-col"><h4>Framework</h4><ul><li>Role Boundaries</li><li>SPV Structure</li><li>Escrow Model</li><li>Records and Registers</li><li>Risk and Boundaries</li></ul></div>
      <div class="foot-col"><h4>Company</h4><ul><li>About</li><li>Leadership</li><li>Governance</li><li>Press</li><li>Careers</li><li>Contact</li></ul></div>
      <div class="foot-col"><h4>Legal</h4><ul><li>Terms of Use</li><li>Privacy Policy</li><li>Cookie Policy</li><li>Disclaimer and Risk Notices</li><li>Acceptable Use</li><li>Accessibility</li></ul></div>
    </div>
    <div class="foot-rule"></div>
    <div class="foot-legal">
      <p>© 2026 The Copper Lantern. All rights reserved.</p>
      <p>This website provides informational content only. The Copper Lantern does not provide investment advice, execute projects, or facilitate transactions. All operational activities are conducted through Halvemark, a separate platform.</p>
    </div>
  </footer>

</main>
</body>
</html>
```